Boutique Technology Consultancy specialising is Electronic and physical security

We need to redo our existing outdated website. For your reference the link www.pelu.com.au

```html
<!DOCTYPE html>
<html lang="en">
<head>
<meta charset="utf-8">
<title>PELU Services</title>
<link rel="stylesheet" href="https://fonts.googleapis.com/css2?family=Poppins:wght@400;500;600;700&display=swap">
<style>
:root{
  --red:#c4202b;
  --red-dark:#9e1b22;
  --ink:#1a1a1a;
  --pink:#fdeff0;
  --grey:#ececec;
  --white:#ffffff;
  --black:#050505;
}
*{margin:0;padding:0;box-sizing:border-box}
html,body{width:1200px;height:4101px;overflow:hidden}
body{font-family:'Poppins',sans-serif;color:var(--ink);background:var(--white);position:relative}
.abs{position:absolute}
/* hero */
.hero{left:0;top:0;width:1200px;height:660px;background:linear-gradient(160deg,#3a3f48 0%,#1d222a 45%,#2c2320 75%,#111 100%)}
.brand{display:flex;align-items:center;gap:10px;color:var(--white);font-weight:700;font-size:48px;letter-spacing:1px}
.brand .mark{width:26px;height:26px;border-radius:50%;background:var(--red)}
.brand small{display:block;font-size:11px;letter-spacing:6px;font-weight:500;text-align:center;margin-top:-6px}
.nav{left:370px;top:42px;display:flex;gap:42px;color:var(--white);font-size:19px;font-weight:500}
.hero-title{left:0;width:1200px;top:222px;text-align:center;color:var(--white);font-weight:700;font-size:49px;line-height:62px}
.hero-sub{left:0;width:1200px;top:350px;text-align:center;color:var(--white);font-size:23px;line-height:28px}
.btn{background:var(--red);color:var(--white);border-radius:30px;display:flex;align-items:center;justify-content:center;font-weight:500}
.hero-btn{left:476px;top:434px;width:226px;height:44px;font-size:19px}
/* section heads */
.sec-head{left:0;width:1200px;display:flex;align-items:center;justify-content:center;gap:14px;color:var(--red-dark);font-weight:700;font-size:44px}
.sec-head::before,.sec-head::after{content:"";width:120px;height:2px;background:var(--red-dark)}
/* services */
.card{width:254px;height:365px;top:820px;background:var(--white);box-shadow:0 2px 10px rgba(0,0,0,.13);padding:28px 14px 0 14px}
.card h3{color:var(--red);font-size:22px;line-height:28px;font-weight:600;height:56px;display:flex;align-items:flex-end;margin-top:58px;width:186px;border-bottom:2px solid var(--red-dark);padding-bottom:10px;box-sizing:content-box}
.card ul{list-style:none;font-size:14px;font-weight:500;margin-top:14px}
.card li{height:35px;line-height:35px}
.card .more{position:absolute;left:14px;bottom:16px;color:var(--red);font-size:22px;font-weight:500}
.card .icon{position:absolute;left:14px;top:28px}
/* who we are */
.who{left:0;top:1295px;width:1200px;height:542px;background:var(--pink)}
.who h2{left:54px;top:70px;color:var(--red-dark);font-size:44px;font-weight:700;display:flex;align-items:center;gap:10px}
.who h2::after{content:"";width:118px;height:2px;background:var(--red-dark)}
.who p{left:58px;width:500px;font-size:14.5px;font-weight:500;line-height:19px;text-transform:uppercase}
.who .btn{left:58px;top:393px;width:228px;height:44px;font-size:19px}
.who-photo{left:653px;top:57px;width:430px;height:430px;border-radius:50%;background:radial-gradient(circle at 50% 45%,#4b6a88,#1f3147 60%,#0c1622)}
/* team */
.member{width:256px;top:2305px;height:165px;background:var(--white);box-shadow:0 2px 10px rgba(0,0,0,.13);text-align:center;padding-top:20px}
.member h4{color:var(--red-dark);font-size:22px;font-weight:600}
.member p{font-size:15px;margin:8px auto 0;width:200px;padding-bottom:8px;border-bottom:1px solid var(--red-dark)}
.member .social{display:flex;justify-content:center;gap:20px;margin-top:20px}
.member .social span{width:26px;height:26px;border:2.5px solid var(--red);border-radius:50%}
.portrait{top:2038px;width:300px;height:300px;background:linear-gradient(180deg,#bfbab3,#6e6860)}
.arrow{width:28px;height:28px;border-radius:50%;background:var(--red);top:2192px}
/* expertise */
.expertise{left:0;top:2555px;width:1200px;height:570px;background:var(--pink)}
.tile{top:190px;width:251px;height:252px;display:flex;flex-direction:column;align-items:center;justify-content:center;text-align:center;color:var(--white);font-weight:600;font-size:22px;line-height:28px;text-transform:uppercase;padding:0 14px}
.tile small{text-transform:none;font-size:10.5px;font-weight:400;line-height:13px;margin-top:12px}
.dots{left:478px;top:507px;display:flex;gap:18px}
.dots span{width:62px;height:8px;background:var(--red-dark)}
.dots span.on{background:none;border:2px solid var(--red-dark)}
/* contact */
.form{left:207px;top:3263px;width:811px;height:407px;border:1px solid #e6e6e6;border-radius:18px;background:var(--white)}
.field{background:var(--grey);color:var(--red-dark);font-size:15px;padding:0 18px;display:flex;align-items:center;height:40px;width:330px}
.field.msg{align-items:flex-start;padding-top:14px;width:695px;height:86px}
.submit{left:50px;top:320px;width:695px;height:52px;background:linear-gradient(90deg,var(--red),#2a1a1b);color:var(--white);font-size:17px;font-weight:500;display:flex;align-items:center;justify-content:center}
/* footer */
.footer{left:0;top:3735px;width:1200px;height:366px;background:var(--black);color:var(--white)}
.footer h5{color:var(--red);font-size:22px;font-weight:500}
.footer ul{list-style:none;font-size:18px;margin-top:14px}
.footer li{line-height:37px;padding-left:26px;position:relative}
.footer li::before{content:"";position:absolute;left:0;top:15px;width:9px;height:9px;border-radius:50%;background:var(--red)}
.qc{display:flex;gap:12px;margin-top:16px;font-size:12px;line-height:15px}
.qc svg{flex:none}
.qc b{display:block;color:var(--red);font-weight:500;font-size:11px}
</style>
</head>
<body>

<!-- HERO -->
<section class="abs hero" role="img" aria-label="Low-angle view of glass office towers against the sky"></section>
<div class="abs brand" style="left:36px;top:22px"><span class="mark"></span><div>PELU<small>SERVICES</small></div></div>
<nav class="abs nav"><span>WELCOME</span><span>EXPERIENCE</span><span>SERVICES</span><span>TEAM</span><span>ABOUT</span><span>CONTACT</span></nav>
<h1 class="abs hero-title">YOUR TECHNOLOGY<br>PROJECTS MADE EASY</h1>
<p class="abs hero-sub">PELU is a privately owned independent consultancy<br>100% dedicated to customer satisfaction.</p>
<a class="abs btn hero-btn">CONTACT US</a>
<svg class="abs" style="left:0;top:628px" width="580" height="32"><polygon points="0,0 580,24 0,32" fill="#b11d25"/></svg>

<!-- WHAT WE DO -->
<h2 class="abs sec-head" style="top:725px">WHAT WE DO</h2>

<div class="abs card" style="left:44px">
  <svg class="icon" width="84" height="80" viewBox="0 0 84 80" fill="none" stroke="#c4202b" stroke-width="3"><rect x="4" y="14" width="56" height="40"/><path d="M14 44v-10M24 44v-16M34 44v-22M44 44v-28"/><circle cx="58" cy="58" r="12"/><path d="M66 66l12 12"/></svg>
  <h3>STRATEGY</h3>
  <ul><li>TECHNOLOGY ROADMAPS</li><li>MASTER STANDARDS</li><li>ASSET MANAGEMENT PLANS</li></ul>
  <span class="more">READ MORE ➚</span>
</div>
<div class="abs card" style="left:328px">
  <svg class="icon" width="84" height="80" viewBox="0 0 84 80" fill="none" stroke="#c4202b" stroke-width="3"><rect x="6" y="4" width="48" height="70"/><circle cx="30" cy="26" r="10"/><path d="M14 48h30M14 58h22M72 30L48 66l-4 8 8-4 24-36z"/></svg>
  <h3>PROJECTS</h3>
  <ul><li>AUDIT</li><li>DESIGN</li><li>WITNESS TESTING</li></ul>
  <span class="more">READ MORE ➚</span>
</div>
<div class="abs card" style="left:612px">
  <svg class="icon" width="84" height="80" viewBox="0 0 84 80" fill="none" stroke="#c4202b" stroke-width="3"><circle cx="36" cy="36" r="22"/><circle cx="36" cy="36" r="9"/><path d="M36 6v8M36 58v8M6 36h8M58 36h8M24 60l-6 16M48 60l6 16"/></svg>
  <h3>OPERATIONS &amp; MAINTENANCE</h3>
  <ul><li>SERVICES</li><li>MAINTENANCE</li><li>POLICIES &amp; PROCEDURES</li></ul>
  <span class="more">READ MORE ➚</span>
</div>
<div class="abs card" style="left:896px">
  <svg class="icon" width="84" height="80" viewBox="0 0 84 80" fill="none" stroke="#c4202b" stroke-width="3"><circle cx="38" cy="38" r="18"/><rect x="30" y="36" width="16" height="12"/><path d="M33 36v-5a5 5 0 0 1 10 0v5M38 4v14M38 58v16M4 38h16M56 38h18"/><circle cx="38" cy="4" r="3"/><circle cx="4" cy="38" r="3"/><circle cx="74" cy="38" r="3"/></svg>
  <h3>OTHER SERVICES</h3>
  <ul><li>CCTV</li><li>SYSTEM INTEGRATION</li><li>SMART CARDS</li></ul>
  <span class="more">READ MORE ➚</span>
</div>

<!-- WHO WE ARE -->
<section class="abs who">
  <h2 class="abs">WHO WE ARE</h2>
  <p class="abs" style="top:153px">PELU Services was established in 2016 by Daniel Corrow to provide technology consulting services to corporate and government clients.</p>
  <p class="abs" style="top:251px;width:490px">PELU is a privately owned independent consultancy 100% dedicated to customer satisfaction. With experience in a range of technologies such as internet of things, security systems, Wi-Fi, building services networks, control centres and smart buildings</p>
  <a class="abs btn">READ MORE</a>
  <div class="abs who-photo" role="img" aria-label="City skyline at night with glowing security shield symbols"></div>
</section>

<!-- OUR TEAM -->
<h2 class="abs sec-head" style="top:1905px">OUR TEAM</h2>
<div class="abs arrow" style="left:30px"></div>
<div class="abs arrow" style="left:1144px"></div>
<div class="abs portrait" style="left:86px" role="img" aria-label="Portrait photo of Daniel Corrow"></div>
<div class="abs portrait" style="left:448px" role="img" aria-label="Portrait photo of Graham Vesty"></div>
<div class="abs portrait" style="left:811px;background:linear-gradient(180deg,#e8e6e4,#bdb7b0)" role="img" aria-label="Portrait photo of Mei Lindqvist"></div>
<div class="abs member" style="left:107px"><h4>DANIEL CORROW</h4><p>Principal Consultant</p><div class="social"><span></span><span></span><span></span></div></div>
<div class="abs member" style="left:470px"><h4>GRAHAM VESTY</h4><p>Principal Consultant</p><div class="social"><span></span><span></span><span></span></div></div>
<div class="abs member" style="left:833px"><h4>MEI LINDQVIST</h4><p>Administration Coordinator</p><div class="social"><span></span><span></span><span></span></div></div>

<!-- EXPERTISE -->
<svg class="abs" style="left:620px;top:2532px" width="580" height="40"><polygon points="580,0 580,40 0,24" fill="#b11d25"/></svg>
<section class="abs expertise">
  <h2 class="abs sec-head" style="top:83px">EXPERTISE</h2>
  <div class="abs tile" style="left:36px;background:linear-gradient(180deg,#8a4a4d,#5e2a2d)" role="img" aria-label="Shopping centre interior with glass dome">Harbour Central<small>Security technology design consulting for his popular retail and entertainment hub which is managed by the Alder Group.</small></div>
  <div class="abs tile" style="left:323px;background:linear-gradient(180deg,#b88a8c,#7a4c4f)" role="img" aria-label="Motorway with gantry and passing cars">Ridge Link</div>
  <div class="abs tile" style="left:615px;background:linear-gradient(180deg,#c9a3a5,#7d4d50)" role="img" aria-label="Tall glass office towers">Meridian Towers</div>
  <div class="abs tile" style="left:901px;background:linear-gradient(180deg,#b07f82,#6e3f42)" role="img" aria-label="Hospital building entrance">Northside Hospital</div>
  <div class="abs dots"><span></span><span class="on"></span><span></span></div>
</section>

<!-- CONTACT -->
<h2 class="abs sec-head" style="top:3163px">CONTACT US</h2>
<form class="abs form">
  <div class="abs field" style="left:53px;top:74px">Your Name</div>
  <div class="abs field" style="left:418px;top:74px">Your Phone</div>
  <div class="abs field" style="left:53px;top:142px">Email Address</div>
  <div class="abs field" style="left:418px;top:142px">Select Service</div>
  <div class="abs field msg" style="left:53px;top:209px">Additional Message</div>
  <div class="abs submit">GET AN APPOINTMENT NOW</div>
</form>

<!-- FOOTER -->
<svg class="abs" style="left:0;top:3718px" width="580" height="20"><polygon points="0,0 580,18 0,20" fill="#b11d25"/></svg>
<footer class="abs footer">
  <div class="abs brand" style="left:58px;top:70px"><span class="mark"></span><div>PELU<small>SERVICES</small></div></div>
  <p class="abs" style="left:58px;top:182px;width:310px;font-size:16px;line-height:19px">PELU is a privately owned independent consultancy 100% dedicated to customer satisfaction.</p>
  <div class="abs" style="left:458px;top:98px"><h5>PAGES</h5><ul><li>Home</li><li>About</li><li>Services</li><li>Contat</li></ul></div>
  <div class="abs" style="left:688px;top:100px"><h5>SERVICES</h5><ul><li>Roadmaps</li><li>Audits</li><li>Designs</li><li>Project<br>Management</li></ul></div>
  <div class="abs" style="left:922px;top:104px"><h5>QUICK CONTACT</h5>
    <div class="qc"><svg width="26" height="26"><circle cx="13" cy="13" r="13" fill="#c4202b"/><path d="M9 7l3 3-2 2a9 9 0 0 0 4 4l2-2 3 3-2 2c-5 0-10-5-10-10z" fill="#fff"/></svg><div><b>PHONE</b>1300 555 018</div></div>
    <div class="qc"><svg width="26" height="26"><circle cx="13" cy="13" r="13" fill="#c4202b"/><rect x="7" y="9" width="12" height="9" fill="#fff"/><path d="M7 9l6 5 6-5" stroke="#c4202b" fill="none"/></svg><div><b>EMAIL</b>hello@pelu.com.au</div></div>
    <div class="qc"><svg width="26" height="26"><circle cx="13" cy="13" r="13" fill="#c4202b"/><path d="M13 20s-5-5-5-8a5 5 0 0 1 10 0c0 3-5 8-5 8z" fill="#fff"/></svg><div><b>LOCATION</b>PO Box 4410<br>CARLTON VIC 3053</div></div>
  </div>
</footer>

</body>
</html>
```